Coastal Learner Bureau business cards

Australian company about to start offering its services. We recruit international students to come to study English, vocational education and postgraduate courses in Australia. We help them find the institution and select the right city they want to come to Australia. We are a young, online oriented and supportive agency. Our clients are between 18 and 35 years old, mainly University students, young professionals or people with work experience. We provide much more information that any other agency offer. We administrate a Facebook group with more than 11.000 members that daily ask questions about general information when coming to Australia, while they are here and even after they leave the country

Target Market(s)

International students from South America, Central America and Europe

Industry/Entity Type

Student

Contact Information for Business Card

Tomas Bilbrea
Managing Director
tomas@kelvarin.com.au
www.kelvoria.com.au
+61 491058264
Melbourne, Australia

Font styles to use
Serif
Sans Serif

Colors

Designer to choose colors to be used in the design.

Requirements
Must have
• Horizontal design
• Standard business card size and shape. If font uses green or yellow colours, they will have to match the ones from the logo
Nice to have
• UPDATE: Use the contents of the green image to design one of the card sides. Use our logo in the background of that side as watermark.
• Passport image, or immigration stamps. A picture of the Yarra River (from Melbourne) would be cool as well.
Should not have
• Non-standard business card size and shape
• Not black as the background colour of any sides as we are not a VIP agency or a hight class service. We are orientes to young people and they like colours, pictures, something attractive.
• Vertical design
• NO YELLOW or BLACK AS THE BACKGROUND COLOUR OF ANY SIDE OF THE BIZ CARD

```html
<!DOCTYPE html>
<html lang="en">
<head>
<meta charset="utf-8">
<title>Coastal Learner Bureau – Business Cards</title>
<link rel="stylesheet" href="https://fonts.googleapis.com/css2?family=Source+Sans+3:wght@400;600&family=Tinos:wght@700&display=swap">
<style>
  :root {
    --backdrop: #6d6d6d;
    --backdrop-light: #666666;
    --card-white: #ffffff;
    --brand-green: #1b5c3a;
    --card-green: #186141;
    --brand-yellow: #e6b71c;
    --ink: #222222;
    --divider: #d6d6d6;
  }
  * { margin: 0; padding: 0; box-sizing: border-box; }
  html, body { width: 1200px; height: 900px; overflow: hidden; }
  body {
    position: relative;
    background: linear-gradient(180deg, var(--backdrop-light) 0%, var(--backdrop) 100%);
    font-family: "Source Sans 3", Arial, sans-serif;
  }
  .card {
    position: absolute;
    top: 306px;
    width: 440px;
    height: 271px;
    border-radius: 12px;
    overflow: hidden;
  }
  .card--front { left: 149px; background: var(--card-white); }
  .card--back { left: 608px; background: var(--card-green); }

  .brand-block {
    position: absolute;
    left: 20px;
    top: 60px;
    width: 200px;
    text-align: center;
  }
  .brand-name {
    font-weight: 600;
    font-size: 27px;
    line-height: 1.05;
    color: var(--brand-green);
    display: block;
  }
  .tagline {
    margin-top: 42px;
    font-family: "Tinos", "Times New Roman", serif;
    font-weight: 700;
    font-size: 14.5px;
    letter-spacing: 0.3px;
    color: var(--brand-green);
  }
  .divider {
    position: absolute;
    left: 230px;
    top: 64px;
    width: 1px;
    height: 142px;
    background: linear-gradient(180deg, transparent, var(--divider) 20%, var(--divider) 80%, transparent);
  }
  .contact {
    position: absolute;
    left: 250px;
    top: 72px;
    color: var(--ink);
  }
  .person-name {
    font-weight: 600;
    font-size: 15.5px;
    line-height: 18px;
    letter-spacing: 0.2px;
  }
  .person-name .first { color: var(--brand-yellow); }
  .person-name .last { color: var(--brand-green); }
  .person-role { font-size: 12.5px; line-height: 16px; }
  .contact-list { list-style: none; margin-top: 16px; }
  .contact-list li {
    display: flex;
    align-items: center;
    gap: 5px;
    font-size: 12.5px;
    line-height: 16px;
  }
  .contact-list svg { width: 9px; height: 9px; fill: var(--brand-yellow); flex: none; }
  .location { margin-top: 11px; font-size: 12.5px; }

  .back-brand {
    position: absolute;
    inset: 0;
    display: flex;
    align-items: center;
    justify-content: center;
    text-align: center;
    font-weight: 600;
    font-size: 40px;
    line-height: 1.05;
    color: var(--card-white);
  }
</style>
</head>
<body>
  <section class="card card--front" aria-label="Business card front">
    <div class="brand-block">
      <span class="brand-name">Coastal Learner<br>Bureau</span>
      <p class="tagline">HACEMOS MÁS POR TI!</p>
    </div>
    <div class="divider"></div>
    <div class="contact">
      <p class="person-name"><span class="first">TOMAS</span> <span class="last">BILBREA</span></p>
      <p class="person-role">Managing Director</p>
      <ul class="contact-list">
        <li>
          <svg viewBox="0 0 10 10" aria-hidden="true"><path d="M2 0.5 L3.6 0.5 L4.3 2.8 L3.1 3.8 C3.7 5.1 4.9 6.3 6.2 6.9 L7.2 5.7 L9.5 6.4 L9.5 8 C9.5 9 8.7 9.5 8 9.5 C4 9.2 0.8 6 0.5 2 C0.5 1.3 1 0.5 2 0.5 Z"/></svg>
          +61 491058264
        </li>
        <li>
          <svg viewBox="0 0 10 10" aria-hidden="true"><path d="M0.5 2 L9.5 2 L9.5 8 L0.5 8 Z M1.2 2.6 L5 5.4 L8.8 2.6"/></svg>
          tomas@kelvarin.com.au
        </li>
        <li>
          <svg viewBox="0 0 10 10" aria-hidden="true"><circle cx="5" cy="5" r="4.5"/></svg>
          www.kelvoria.com.au
        </li>
      </ul>
      <p class="location">Melbourne, Australia</p>
    </div>
  </section>

  <section class="card card--back" aria-label="Business card back">
    <span class="back-brand">Coastal Learner<br>Bureau</span>
  </section>
</body>
</html>
```